Help design website for "Brightwater Civic Advisors" to advance the common good

Here is the Google doc link that lays out the design:

https://files.plumrivet.example/sheet/d/7QmTzR2wLx9KpVbN4hJcY8sEaUoFdG3iXkMnPq5rWt6/edit?usp=sharing

Here is the Google drive folder with the logos and photos: https://vault.plumrivet.example/open?id=4HkWp9LzQe2TxRvN8mBaYc3DsUoJfG6

The testimonials are being gathered and will be shared by Friday, 1/4.

The winner will also have to migrate the coding files to my hosting site.

Thank you for your help! Looking forward to seeing your designs.

Target Market(s)

Prospective clients

Industry/Entity Type

Non Profit

Coding

Coded - Design and coding required

Number of Pages Required

5+ page

Requirements
Must have
• Noted in the Google doc regarding layout.
Nice to have

```html
<!DOCTYPE html>
<html lang="en">
<head>
<meta charset="utf-8">
<title>Brightwater Civic Advisors</title>
<link rel="stylesheet" href="https://fonts.googleapis.com/css2?family=Montserrat:wght@400;500;600;700&family=Mulish:wght@400;600;700&display=swap">
<style>
:root{
  --blue:#3a86c8;
  --blue-dark:#2f6fa8;
  --ink:#2b2b2b;
  --text:#444;
  --muted:#777;
  --grey:#efefef;
  --white:#fff;
  --dark:#1c2430;
}
*{box-sizing:border-box;margin:0;padding:0}
html,body{width:1200px;height:3742px;overflow:hidden}
body{position:relative;background:var(--white);font-family:"Mulish",sans-serif;color:var(--text)}
.abs{position:absolute}
h2.section-title{position:absolute;left:0;width:1200px;text-align:center;font-family:"Montserrat",sans-serif;font-weight:600;font-size:32px;color:var(--blue);letter-spacing:.5px}

/* header */
.site-header{position:absolute;top:0;left:0;width:1200px;height:115px;background:var(--white)}
.contact-chip{position:absolute;top:18px;display:flex;gap:14px;align-items:flex-start}
.chip-icon{width:40px;height:40px;background:var(--blue);border-radius:4px;display:flex;align-items:center;justify-content:center}
.chip-label{font-size:13px;color:var(--blue);font-weight:700}
.chip-value{font-size:16px;color:var(--ink);margin-top:4px}
.main-nav{position:absolute;top:80px;left:98px;display:flex;gap:30px;font-family:"Montserrat",sans-serif;font-size:16px;color:var(--ink);font-weight:500}
.brand{position:absolute;top:14px;left:790px;display:flex;align-items:center;gap:16px}
.brand-mark{width:70px;height:70px;background:var(--blue)}
.brand-name{font-family:"Montserrat",sans-serif;font-weight:500;font-size:22px;line-height:25px;letter-spacing:5px;color:var(--ink)}

/* hero */
.hero{position:absolute;top:115px;left:0;width:1200px;height:640px;background:linear-gradient(180deg,#4a3a30 0%,#3a2d26 45%,#2a2420 100%)}
.hero-copy{position:absolute;top:200px;left:0;width:1200px;text-align:center;color:var(--white)}
.hero-copy .pre{font-family:"Montserrat",sans-serif;font-size:40px;font-weight:400;letter-spacing:1px}
.hero-copy h1{font-family:"Montserrat",sans-serif;font-size:42px;font-weight:700;letter-spacing:1px;margin-top:2px}
.hero-copy p{font-size:22px;line-height:34px;margin:12px auto 0;width:860px}
.hero-buttons{position:absolute;top:395px;left:0;width:1200px;display:flex;justify-content:center;gap:22px}
.btn-outline{width:186px;height:54px;border:2px solid var(--white);border-radius:28px;display:flex;align-items:center;justify-content:center;gap:10px;color:var(--white);font-family:"Montserrat",sans-serif;font-weight:600;font-size:17px}

/* about */
.about-copy{position:absolute;top:840px;left:90px;width:476px}
.about-copy h2{font-family:"Montserrat",sans-serif;font-size:32px;font-weight:600;color:var(--blue)}
.about-copy p{font-size:15px;line-height:31px;color:var(--text);text-align:justify;margin-top:10px}
.about-copy p+p{margin-top:0}
.btn-small{display:inline-flex;align-items:center;gap:6px;margin-top:24px;height:44px;padding:0 22px;border:2px solid var(--blue);border-radius:24px;color:var(--blue);font-weight:700;font-size:15px}
.photo-circle{position:absolute;border-radius:50%}

/* services */
.band-grey{position:absolute;left:0;width:1200px;background:var(--grey)}
.service-card{position:absolute;top:1540px;width:322px}
.service-photo{width:322px;height:205px}
.service-card h3{margin-top:18px;font-family:"Montserrat",sans-serif;font-size:16px;line-height:25px;font-weight:700;color:var(--blue);text-transform:uppercase}
.service-card p{margin-top:6px;font-size:15px;line-height:29px;height:58px;overflow:hidden;color:var(--text)}
.slide-arrow{position:absolute;width:34px;height:34px;border:2px solid var(--blue);border-radius:50%;display:flex;align-items:center;justify-content:center}

/* testimonials */
.quote{position:absolute;top:2150px;left:165px;width:870px;text-align:center;font-size:15px;line-height:28px;color:var(--text)}
.quote-author{position:absolute;top:2290px;left:0;width:1200px;text-align:center;font-family:"Montserrat",sans-serif;font-weight:700;font-size:15px;color:var(--ink)}

/* articles */
.article-photo{position:absolute;width:460px;height:256px}
.article-photo .frame{position:absolute;inset:14px;border:4px solid var(--white)}
.article-card{position:absolute;width:460px;height:256px;background:var(--white);border:2px solid #cfcfcf;padding:20px 20px}
.article-date{font-size:12px;color:var(--muted);display:flex;align-items:center;gap:6px}
.article-card h3{margin-top:14px;font-family:"Montserrat",sans-serif;font-size:16px;line-height:24px;font-weight:700;color:var(--blue);text-transform:uppercase}
.article-card p{margin-top:10px;font-size:13px;line-height:22px;color:var(--muted);height:88px;overflow:hidden}
.read-more{margin-top:12px;font-size:11px;font-weight:700;color:var(--blue)}

/* footer */
.site-footer{position:absolute;top:3240px;left:0;width:1200px;height:502px;background:linear-gradient(180deg,#2c3644 0%,#1f2833 60%,#161c25 100%)}
.footer-col{position:absolute;color:var(--white)}
.footer-col h4{font-family:"Montserrat",sans-serif;font-size:16px;font-weight:700;letter-spacing:.3px}
.footer-col .note{font-size:12px;margin-top:20px}
.field{position:absolute;width:196px;height:40px;border:2px solid var(--white);color:var(--white);font-size:11px;font-weight:700;padding:13px 10px}
.submit{position:absolute;width:196px;height:40px;background:var(--blue);color:var(--white);font-size:13px;font-weight:700;display:flex;align-items:center;justify-content:center}
.quick-links{list-style:none;margin-top:18px}
.quick-links li{font-size:14px;line-height:27px}
.quick-links li::before{content:"»";margin-right:10px}
.contact-list{list-style:none;margin-top:18px;font-size:14px;line-height:27px}
.contact-list li{display:flex;gap:12px}
.social-dots{display:flex;gap:8px;margin-top:10px}
.social-dots span{width:14px;height:14px;border-radius:50%;background:var(--white)}
.footer-rule{position:absolute;top:3690px;left:90px;width:1020px;height:1px;background:rgba(255,255,255,.35)}
.copyright{position:absolute;top:3706px;left:0;width:1200px;text-align:center;font-size:13px;color:var(--white)}
</style>
</head>
<body>

<header class="site-header">
  <div class="contact-chip" style="left:98px">
    <div class="chip-icon"><svg width="20" height="20" viewBox="0 0 24 24"><path fill="#fff" d="M6.6 10.8a15 15 0 0 0 6.6 6.6l2.2-2.2c.3-.3.7-.4 1-.2 1.1.4 2.3.6 3.6.6.6 0 1 .4 1 1V20c0 .6-.4 1-1 1A17 17 0 0 1 3 4c0-.6.4-1 1-1h3.5c.6 0 1 .4 1 1 0 1.3.2 2.5.6 3.6.1.3 0 .7-.2 1z"/></svg></div>
    <div><div class="chip-label">Call us anytime</div><div class="chip-value">555 010 2040</div></div>
  </div>
  <div class="contact-chip" style="left:298px">
    <div class="chip-icon"><svg width="20" height="20" viewBox="0 0 24 24"><path fill="#fff" d="M3 6h18v12H3z"/><path fill="none" stroke="#3a86c8" stroke-width="2" d="M3 6l9 7 9-7"/></svg></div>
    <div><div class="chip-label">Send us a mail</div><div class="chip-value">info@brightwatercivic.example</div></div>
  </div>
  <nav class="main-nav"><span>Home</span><span>About</span><span>Services &amp; Testimonials</span><span>Media &amp; Impact</span><span>Contact</span></nav>
  <div class="brand"><div class="brand-mark"></div><div class="brand-name">BRIGHTWATER<br>CIVIC<br>ADVISORS</div></div>
</header>

<section class="hero" role="img" aria-label="Photo of a group of students and facilitators talking around tables">
  <div class="hero-copy">
    <div class="pre">WELCOME TO</div>
    <h1>BRIGHTWATER CIVIC ADVISORS</h1>
    <p>Sed ut perspiciatis unde omnis iste natus error sit voluptatem accusantium doloremque laudantium, totam rem aperiam</p>
  </div>
  <div class="hero-buttons">
    <div class="btn-outline"><svg width="18" height="18" viewBox="0 0 24 24"><circle cx="12" cy="12" r="7" fill="none" stroke="#fff" stroke-width="4" stroke-dasharray="3 2.5"/><circle cx="12" cy="12" r="3" fill="#fff"/></svg>Our Services</div>
    <div class="btn-outline"><svg width="18" height="18" viewBox="0 0 24 24"><path fill="#fff" d="M22 2 2 10l8 3 3 8z"/></svg>Contact us</div>
  </div>
</section>
<svg class="abs" style="top:650px;left:0" width="1200" height="110" viewBox="0 0 1200 110">
  <polygon points="0,16 600,100 1200,16 1200,110 0,110" fill="#3a86c8"/>
  <polygon points="0,26 600,86 1200,26 1200,110 0,110" fill="#fff"/>
</svg>

<section class="about">
  <div class="about-copy">
    <h2>ABOUT US</h2>
    <p>Brightwater Civic Advisors supports nonprofit organizations and educational institutions to carry out their missions to benefit the wider community.</p>
    <p>Founder Dana Whitfield is an educator with a 22-year record of demonstrated achievement and leadership roles in nonprofits and educational institutions. Most recently, she served as Associate Dean of Students in the University and Director of the University Community Service Center at Lakeshore University.</p>
    <div class="btn-small"><svg width="12" height="14" viewBox="0 0 12 14"><path fill="#3a86c8" d="M0 0h8l4 4v10H0z"/></svg>Read More</div>
  </div>
  <div class="photo-circle" role="img" aria-label="Photo of a group of smiling students" style="left:827px;top:765px;width:300px;height:300px;background:linear-gradient(135deg,#8a7a6a,#4f4a46)"></div>
  <div class="photo-circle" role="img" aria-label="Photo of students gathered outdoors" style="left:900px;top:1088px;width:226px;height:226px;background:linear-gradient(135deg,#b9aea2,#7c746c)"></div>
  <div class="photo-circle" role="img" aria-label="Portrait of the founder" style="left:630px;top:848px;width:420px;height:420px;background:linear-gradient(135deg,#a08b72,#5d5347);border:5px solid #fff"></div>
</section>

<svg class="abs" style="top:1300px;left:0" width="1200" height="95" viewBox="0 0 1200 95">
  <polygon points="0,88 600,0 1200,88 1200,95 0,95" fill="#3a86c8"/>
  <polygon points="0,95 600,14 1200,95" fill="#efefef"/>
</svg>
<section class="band-grey" style="top:1393px;height:612px"></section>
<h2 class="section-title" style="top:1458px">OUR SERVICES</h2>
<div class="slide-arrow" style="left:33px;top:1700px"><svg width="12" height="12" viewBox="0 0 12 12"><path d="M8 1 3 6l5 5" fill="none" stroke="#3a86c8" stroke-width="2"/></svg></div>
<div class="slide-arrow" style="left:1133px;top:1700px"><svg width="12" height="12" viewBox="0 0 12 12"><path d="M4 1l5 5-5 5" fill="none" stroke="#3a86c8" stroke-width="2"/></svg></div>
<article class="service-card" style="left:90px">
  <div class="service-photo" role="img" aria-label="Photo of staff members posing together with colourful props" style="background:linear-gradient(135deg,#5a4b52,#2e2a30)"></div>
  <h3>Staff Professional<br>Development</h3>
  <p>Dana has supervised, coached, and mentored hundreds of staff members, including professionals and students.</p>
</article>
<article class="service-card" style="left:440px">
  <div class="service-photo" role="img" aria-label="Photo of a community group standing beneath large signs" style="background:linear-gradient(135deg,#9a938a,#4a4440)"></div>
  <h3>Community Partnership<br>Development</h3>
  <p>Dana has collaborated with more than 250 nonprofits, schools, government agencies, and businesses with corporate social responsibility.</p>
</article>
<article class="service-card" style="left:790px">
  <div class="service-photo" role="img" aria-label="Photo of a crowded gallery event" style="background:linear-gradient(135deg,#8a6a4a,#3e332a)"></div>
  <h3>Group Facilitation &amp; Leadership<br>Training</h3>
  <p>Dana has facilitated student groups, experiential learning activities, and dialogues on social justice issues, such as race.</p>
</article>

<h2 class="section-title" style="top:2090px">TESTIMONIALS</h2>
<div class="slide-arrow" style="left:33px;top:2188px"><svg width="12" height="12" viewBox="0 0 12 12"><path d="M8 1 3 6l5 5" fill="none" stroke="#3a86c8" stroke-width="2"/></svg></div>
<div class="slide-arrow" style="left:1133px;top:2188px"><svg width="12" height="12" viewBox="0 0 12 12"><path d="M4 1l5 5-5 5" fill="none" stroke="#3a86c8" stroke-width="2"/></svg></div>
<p class="quote">"Dana has an uncanny ability to combine social change theory and real-world practice in truly compelling ways. For five years at Lakeshore University, I saw first-hand how Dana inspired legions of students, created innovative programs, and transformed relationships with community stakeholders. Best of all, she did it with integrity, smarts, enthusiasm and a warm, infectious spirit."</p>
<div class="quote-author">- Marcus Hale, VP, Chief Content Officer, Civic Radio Network</div>

<section class="band-grey" style="top:2375px;height:870px"></section>
<svg class="abs" style="top:2375px;left:0" width="1200" height="100" viewBox="0 0 1200 100">
  <polygon points="0,0 1200,0 1200,12 600,88 0,12" fill="#3a86c8"/>
  <polygon points="0,0 1200,0 1200,3 600,70 0,3" fill="#fff"/>
</svg>
<h2 class="section-title" style="top:2520px">OUR ARTICLES</h2>

<div class="article-photo" role="img" aria-label="Photo of students seated at round tables in a hall" style="left:133px;top:2608px;background:linear-gradient(135deg,#7a6656,#3a302a)"><div class="frame"></div></div>
<article class="article-card" style="left:608px;top:2608px">
  <div class="article-date"><svg width="11" height="11" viewBox="0 0 12 12"><circle cx="6" cy="6" r="5" fill="none" stroke="#3a86c8" stroke-width="1.6"/><path d="M6 3v3h2" fill="none" stroke="#3a86c8" stroke-width="1.4"/></svg>Date: Oct. 21, 2018</div>
  <h3>Guest Speaker Leads Students in South Side Day of Action on Global Forum's Last Day</h3>
  <p>Hundreds of students committed to changing the world came to Lakeshore City as part of a Global Youth Forum. On Sunday, they settled for making a difference on the South Side.</p>
  <div class="read-more">READ MORE →</div>
</article>

<article class="article-card" style="left:133px;top:2900px">
  <div class="article-date"><svg width="11" height="11" viewBox="0 0 12 12"><circle cx="6" cy="6" r="5" fill="none" stroke="#3a86c8" stroke-width="1.6"/><path d="M6 3v3h2" fill="none" stroke="#3a86c8" stroke-width="1.4"/></svg>Date: Apr 6, 2018</div>
  <h3>Community and Student Arts Shine at Riverside Park</h3>
  <p>Every year it gets bigger and better," said Renee Okafor, Chief Program Officer of Lakeshore Youth Programs (LYP), about the third annual Riverside Park Arts Festival that took place last Saturday. A collaboration between LYP, Student Government.</p>
  <div class="read-more">READ MORE →</div>
</article>
<div class="article-photo" role="img" aria-label="Photo of a student band performing in a gym" style="left:608px;top:2900px;background:linear-gradient(135deg,#9a8e80,#4c4640)"><div class="frame"></div></div>

<footer class="site-footer" role="img" aria-label="Photo of a large group of participants, darkened behind footer content">
  <svg class="abs" style="top:0;left:0" width="1200" height="100" viewBox="0 0 1200 100">
    <polygon points="0,0 1200,0 1200,84 600,0 0,84" fill="#efefef"/>
    <polygon points="0,84 600,0 1200,84 1200,96 600,13 0,96" fill="#3a86c8"/>
  </svg>
</footer>
<div class="footer-col" style="left:133px;top:3460px">
  <h4>GET IN TOUCH</h4>
  <div class="note">Alternatively You Can Fill In The Following Contact Form:</div>
</div>
<div class="field" style="left:133px;top:3540px">NAME</div>
<div class="field" style="left:342px;top:3540px">EMAIL</div>
<div class="field" style="left:133px;top:3595px">PHONE</div>
<div class="submit" style="left:342px;top:3595px">SUBMIT</div>
<div class="footer-col" style="left:625px;top:3460px">
  <h4>QUICK LINKS</h4>
  <ul class="quick-links"><li>Home</li><li>About</li><li>Services</li><li>Testimonials</li><li>Media &amp; Impact</li><li>Contact</li></ul>
</div>
<div class="footer-col" style="left:838px;top:3460px">
  <h4>CONTACT US</h4>
  <ul class="contact-list">
    <li><svg width="12" height="14" viewBox="0 0 12 16" style="margin-top:6px"><path fill="#fff" d="M6 0a6 6 0 0 1 6 6c0 4-6 10-6 10S0 10 0 6a6 6 0 0 1 6-6z"/></svg><span>Harbor City, ST 00000,<br>United States</span></li>
    <li><svg width="12" height="12" viewBox="0 0 24 24" style="margin-top:7px"><path fill="#fff" d="M6.6 10.8a15 15 0 0 0 6.6 6.6l2.2-2.2c.3-.3.7-.4 1-.2 1.1.4 2.3.6 3.6.6.6 0 1 .4 1 1V20c0 .6-.4 1-1 1A17 17 0 0 1 3 4c0-.6.4-1 1-1h3.5c.6 0 1 .4 1 1 0 1.3.2 2.5.6 3.6.1.3 0 .7-.2 1z"/></svg><span>555 010 2040</span></li>
    <li><svg width="12" height="10" viewBox="0 0 24 18" style="margin-top:9px"><rect width="24" height="18" fill="#fff"/></svg><span>info@brightwatercivic.example</span></li>
  </ul>
  <div class="social-dots"><span></span><span></span><span></span><span></span><span></span></div>
</div>
<div class="footer-rule"></div>
<div class="copyright">Copyrights © 2019. All Rights Reserved</div>

</body>
</html>
```